banner ad

We're looking for a banner similar to the one shown on the attached file. The same 4 keywords, the same text up top, but with new formatting, design and perhaps color scheme. Looking for something to catch people's attention that will stand out on this particular page shown in the attached image. Our goal is to find a banner with a better click through rate than the current version.

```html
<!DOCTYPE html>
<html lang="en">
<head>
<meta charset="utf-8">
<title>Ads Related to blood glucose</title>
<link rel="stylesheet" href="https://fonts.googleapis.com/css2?family=Poppins:wght@400;600;700&display=swap">
<style>
  :root {
    --navy: #14213d;
    --navy-soft: #22335a;
    --white: #ffffff;
    --label: #a9b6d3;
    --canvas: #f3f6fb;
    --cta-start: #ff5a3c;
    --cta-end: #ff9a2e;
    --cta-shadow: rgba(255, 90, 60, 0.35);
    --arrow-bg: rgba(255, 255, 255, 0.22);
    --accent: #ffb23e;
  }
  * { margin: 0; padding: 0; box-sizing: border-box; }
  html, body { width: 1200px; height: 263px; overflow: hidden; background: var(--canvas); }
  .ad-banner {
    width: 1200px;
    height: 263px;
    display: flex;
    flex-direction: column;
    font-family: "Poppins", Arial, sans-serif;
    background: var(--canvas);
  }
  .ad-header {
    height: 58px;
    flex: none;
    background: linear-gradient(90deg, var(--navy), var(--navy-soft));
    display: flex;
    align-items: center;
    justify-content: space-between;
    padding: 0 30px;
    border-bottom: 4px solid var(--accent);
  }
  .ad-title {
    color: var(--white);
    font-size: 24px;
    font-weight: 600;
    letter-spacing: 0.2px;
  }
  .ad-label {
    color: var(--label);
    font-size: 12px;
    font-weight: 600;
    letter-spacing: 2px;
    border: 1px solid var(--label);
    border-radius: 4px;
    padding: 3px 8px;
  }
  .keyword-row {
    flex: 1;
    display: grid;
    grid-template-columns: repeat(4, 1fr);
    gap: 24px;
    padding: 0 30px;
    align-items: center;
  }
  .keyword-card {
    height: 112px;
    border-radius: 16px;
    background: linear-gradient(135deg, var(--cta-start), var(--cta-end));
    box-shadow: 0 8px 18px var(--cta-shadow);
    display: flex;
    align-items: center;
    justify-content: space-between;
    gap: 12px;
    padding: 0 18px 0 22px;
    color: var(--white);
    text-decoration: none;
  }
  .keyword-text {
    font-size: 18px;
    font-weight: 700;
    line-height: 1.25;
    text-transform: uppercase;
  }
  .keyword-arrow {
    flex: none;
    width: 40px;
    height: 40px;
    border-radius: 50%;
    background: var(--arrow-bg);
    display: flex;
    align-items: center;
    justify-content: center;
  }
  .footer-stripe {
    height: 8px;
    flex: none;
    background: linear-gradient(90deg, var(--cta-start), var(--cta-end));
  }
</style>
</head>
<body>
  <div class="ad-banner">
    <header class="ad-header">
      <h1 class="ad-title">Ads Related to blood glucose</h1>
      <span class="ad-label">ADVERTISEMENT</span>
    </header>
    <nav class="keyword-row">
      <a class="keyword-card" href="#">
        <span class="keyword-text">Blood glucose</span>
        <span class="keyword-arrow"><svg width="18" height="18" viewBox="0 0 18 18"><path d="M3 9h11M9 4l5 5-5 5" fill="none" stroke="#fff" stroke-width="2.4" stroke-linecap="round" stroke-linejoin="round"/></svg></span>
      </a>
      <a class="keyword-card" href="#">
        <span class="keyword-text">Normal blood<br>sugar range</span>
        <span class="keyword-arrow"><svg width="18" height="18" viewBox="0 0 18 18"><path d="M3 9h11M9 4l5 5-5 5" fill="none" stroke="#fff" stroke-width="2.4" stroke-linecap="round" stroke-linejoin="round"/></svg></span>
      </a>
      <a class="keyword-card" href="#">
        <span class="keyword-text">Blood sugar<br>levels chart</span>
        <span class="keyword-arrow"><svg width="18" height="18" viewBox="0 0 18 18"><path d="M3 9h11M9 4l5 5-5 5" fill="none" stroke="#fff" stroke-width="2.4" stroke-linecap="round" stroke-linejoin="round"/></svg></span>
      </a>
      <a class="keyword-card" href="#">
        <span class="keyword-text">What is normal<br>blood sugar?</span>
        <span class="keyword-arrow"><svg width="18" height="18" viewBox="0 0 18 18"><path d="M3 9h11M9 4l5 5-5 5" fill="none" stroke="#fff" stroke-width="2.4" stroke-linecap="round" stroke-linejoin="round"/></svg></span>
      </a>
    </nav>
    <div class="footer-stripe"></div>
  </div>
</body>
</html>
```